Oil and Gas Exploration and Production company needs a business card design

We need a business card design using our logo and colors in the logo. We want a mainstream design.

```html
<!DOCTYPE html>
<html lang="en">
<head>
<meta charset="utf-8">
<title>Ardent Oil &amp; Gas – Business Card</title>
<link rel="stylesheet" href="https://fonts.googleapis.com/css2?family=Roboto:wght@400;500;700;900&display=swap">
<style>
  :root {
    --stage: #808080;
    --card-white: #ffffff;
    --card-black: #1f1d1e;
    --ink: #1a1a1a;
    --gold: #d4a233;
    --back-mark: #8d8b8c;
  }
  * { margin: 0; padding: 0; box-sizing: border-box; }
  html, body { width: 1200px; height: 900px; overflow: hidden; }
  body {
    background: var(--stage);
    font-family: 'Roboto', sans-serif;
    position: relative;
  }
  .card {
    position: absolute;
    width: 540px;
    height: 309px;
    border-radius: 24px;
    overflow: hidden;
    box-shadow: 0 12px 30px rgba(0,0,0,0.35);
  }
  .card--front { left: 40px; top: 296px; background: var(--card-white); }
  .card--back  { left: 620px; top: 296px; background: var(--card-black); }

  .front-waves { position: absolute; inset: 0; }

  .brand {
    position: absolute;
    display: flex;
    align-items: center;
    gap: 10px;
    font-weight: 900;
    white-space: nowrap;
  }
  .brand__dot { border-radius: 50%; flex: none; }
  .brand--front { left: 24px; top: 62px; font-size: 27px; color: var(--ink); letter-spacing: -0.3px; }
  .brand--front .brand__dot { width: 16px; height: 16px; background: var(--ink); }

  .rule {
    position: absolute;
    left: 52px; top: 197px;
    width: 446px; height: 2px;
    background: var(--gold);
  }
  .contact {
    position: absolute;
    left: 22px; top: 214px;
    list-style: none;
    font-size: 13px;
    color: var(--ink);
    line-height: 21px;
  }
  .contact li { display: flex; align-items: center; gap: 7px; }
  .contact svg { width: 10px; height: 10px; fill: var(--gold); flex: none; }
  .contact .accent { color: var(--gold); }

  .person {
    position: absolute;
    right: 44px; top: 138px;
    text-align: right;
  }
  .person__name { font-size: 26px; font-weight: 500; color: var(--gold); line-height: 1.1; }
  .person__role { font-size: 13px; color: var(--ink); margin-top: 3px; }

  .address {
    position: absolute;
    right: 44px; top: 216px;
    text-align: right;
    font-size: 14px;
    font-style: normal;
    line-height: 21px;
    color: var(--ink);
  }

  .brand--back {
    left: 50%; top: 50%;
    transform: translate(-50%, -50%);
    font-size: 44px;
    color: var(--back-mark);
  }
  .brand--back .brand__dot { width: 26px; height: 26px; background: var(--back-mark); }
</style>
</head>
<body>

<section class="card card--front" aria-label="Business card front">
  <svg class="front-waves" viewBox="0 0 540 309" aria-hidden="true">
    <path d="M150,0 L540,0 L540,100 C430,96 350,70 300,40 C260,14 210,0 150,0 Z" fill="var(--card-black)"/>
    <path d="M150,0 C210,0 260,14 300,40 C350,70 430,96 540,100 L540,110 C425,106 342,80 292,50 C252,24 205,6 150,4 Z" fill="var(--gold)"/>
    <path d="M90,0 L150,0 C195,4 235,16 270,34 L266,37 C225,18 180,6 90,0 Z" fill="var(--card-black)"/>
  </svg>

  <div class="brand brand--front">
    <span class="brand__dot"></span>
    <span class="brand__name">Ardent Oil &amp; Gas</span>
  </div>

  <div class="rule"></div>

  <ul class="contact">
    <li><svg viewBox="0 0 10 10"><path d="M2,0 L4,2.5 L3,3.6 C3.8,5.2 4.8,6.2 6.4,7 L7.5,6 L10,8 L8.5,10 C4,9.5 0.5,6 0,1.5 Z"/></svg><span>(555) 014-2287</span></li>
    <li><svg viewBox="0 0 10 10"><path d="M0,2 H10 V8.5 H0 Z M0.8,2.6 L5,5.6 L9.2,2.6" stroke="#fff" stroke-width="0.7"/></svg><span>info@ardentoilgas.com</span></li>
    <li><svg viewBox="0 0 10 10"><circle cx="5" cy="5" r="5"/></svg><span>www.<span class="accent">ardentoilgas</span>.com</span></li>
  </ul>

  <div class="person">
    <p class="person__name">Dale Whitford</p>
    <p class="person__role">CFO</p>
  </div>

  <address class="address">
    4820 Meridian Ave,<br>Midland, Texas US
  </address>
</section>

<section class="card card--back" aria-label="Business card back">
  <div class="brand brand--back">
    <span class="brand__dot"></span>
    <span class="brand__name">Ardent Oil &amp; Gas</span>
  </div>
</section>

</body>
</html>
```